4th Generation Family Business Needs a New Card Design!

We are a family owned 4th Generation company. We are based in the Sydney, Australia area and we are desperately in need of a more modern and classy card. We are monumental masons who design, supply & erect lasting memorials throughout cemeteries in Sydney. Our customers are normally in a period of grieving. I have attached logo files that will need to be implemented on the card. Company was established 1935. Australian Owned and Operated. Card needs to be designed to PIXO.com specification.

Target Market(s)

Our target market is based upon people that a grieving for family members that have passed away. We also deal with alot of companies that own and operate cemeteries.

Industry/Entity Type

Business

Contact Information for Business Card

Simon Harcourt, Operations Manager, 0417293086, simon@harcourtmemorials.com.au
Lewis Harcourt, Director, 0491630572, lewis@harcourtmemorials.com.au
Phone # 02 9561 3048
Website: www.harcourtmemorials.com.au
Address: Suite 17, 8 Palfrey Lane, West Carlow, Sydney NSW 2156

Font styles to use
Serif
Decorative
Script

Requirements
Must have
• Would like to see the logo nicely implemented with a modern design. Embossed lettering would be a nice additive.

```html
<!DOCTYPE html>
<html lang="en">
<head>
<meta charset="utf-8">
<title>Harcourt Memorials – Business Card</title>
<link rel="stylesheet" href="https://fonts.googleapis.com/css2?family=Cinzel:wght@400;600&family=Tinos&display=swap">
<style>
  :root {
    --backdrop: #3f3430;
    --card-black: #1d1d1f;
    --card-charcoal: #2c2c2f;
    --card-white: #ffffff;
    --gold: #f2b705;
    --ink: #161616;
    --text-light: #e9e9e9;
    --emboss: #29292c;
  }
  * { margin: 0; padding: 0; box-sizing: border-box; }
  html, body { width: 1200px; height: 716px; overflow: hidden; }
  body {
    background: var(--backdrop);
    position: relative;
    font-family: "Tinos", "Times New Roman", serif;
  }
  .card {
    position: absolute;
    top: 205px;
    width: 500px;
    height: 306px;
    overflow: hidden;
  }
  .card-back { left: 70px; background: var(--card-black); }
  .card-front { left: 630px; background: var(--card-charcoal); }

  .back-mark {
    position: absolute;
    inset: 0;
    display: flex;
    align-items: center;
    justify-content: center;
    gap: 14px;
  }
  .back-mark .mark-square { width: 30px; height: 30px; background: var(--emboss); }
  .back-mark .mark-name {
    font-family: "Cinzel", serif;
    font-weight: 600;
    font-size: 26px;
    line-height: 1;
    letter-spacing: 2px;
    color: var(--emboss);
  }

  .front-shape { position: absolute; inset: 0; }

  .holder { position: absolute; left: 30px; top: 26px; }
  .holder-name {
    font-family: "Cinzel", serif;
    font-weight: 400;
    font-size: 21px;
    letter-spacing: 1px;
    color: var(--gold);
  }
  .holder-title { font-size: 11px; color: var(--text-light); margin-top: 1px; }

  .contact {
    position: absolute;
    left: 30px;
    top: 150px;
    list-style: none;
    font-size: 12.5px;
    line-height: 17px;
    color: var(--text-light);
  }
  .contact li { display: flex; align-items: center; gap: 7px; white-space: nowrap; }
  .contact .address { padding-left: 17px; margin-bottom: 2px; }
  .contact svg { width: 10px; height: 10px; flex: none; }

  .front-mark {
    position: absolute;
    left: 306px;
    top: 150px;
    display: flex;
    align-items: center;
    gap: 9px;
  }
  .front-mark .mark-square { width: 14px; height: 14px; background: var(--ink); }
  .front-mark .mark-name {
    font-family: "Cinzel", serif;
    font-weight: 600;
    color: var(--ink);
    line-height: 1.1;
  }
  .front-mark .mark-line1 { display: block; font-size: 22px; letter-spacing: 1px; }
  .front-mark .mark-line2 { display: block; font-size: 12px; letter-spacing: 3px; text-align: center; }
</style>
</head>
<body>

<section class="card card-back" aria-label="Card back">
  <div class="back-mark">
    <span class="mark-square"></span>
    <span class="mark-name">HARCOURT MEMORIALS</span>
  </div>
</section>

<section class="card card-front" aria-label="Card front">
  <svg class="front-shape" viewBox="0 0 500 306" width="500" height="306" aria-hidden="true">
    <path d="M250 306 C254 170 336 60 450 0 L500 0 L500 306 Z" fill="var(--card-white)"/>
    <path d="M234 306 C238 160 322 50 434 0" fill="none" stroke="var(--gold)" stroke-width="5"/>
  </svg>

  <header class="holder">
    <h1 class="holder-name">Simon Harcourt</h1>
    <p class="holder-title">Operations Manager</p>
  </header>

  <ul class="contact">
    <li class="address">Suite 17, 8 Palfrey Lane,<br>West Carlow, Sydney NSW 2156</li>
    <li>
      <svg viewBox="0 0 10 10"><rect x="2.5" y="0.5" width="5" height="9" rx="1" fill="var(--gold)"/></svg>
      0417293086
    </li>
    <li>
      <svg viewBox="0 0 10 10"><path d="M2 1 L4 1 L4.6 3 L3.4 4 Q4.5 6 6 6.6 L7 5.4 L9 6 L9 8 Q5 9.5 2 6 Q0.8 3.5 2 1 Z" fill="var(--gold)"/></svg>
      02 9561 3048
    </li>
    <li>
      <svg viewBox="0 0 10 10"><rect x="0.5" y="2" width="9" height="6" fill="var(--gold)"/><path d="M0.5 2 L5 5.5 L9.5 2" fill="none" stroke="var(--card-charcoal)" stroke-width="0.9"/></svg>
      simon@harcourtmemorials.com.au
    </li>
    <li>
      <svg viewBox="0 0 10 10"><circle cx="5" cy="5" r="4.3" fill="none" stroke="var(--gold)" stroke-width="1.2"/><path d="M0.7 5 H9.3 M5 0.7 V9.3" stroke="var(--gold)" stroke-width="0.9"/></svg>
      www.harcourtmemorials.com.au
    </li>
  </ul>

  <div class="front-mark">
    <span class="mark-square"></span>
    <span class="mark-name">
      <span class="mark-line1">HARCOURT</span>
      <span class="mark-line2">MEMORIALS</span>
    </span>
  </div>
</section>

</body>
</html>
```